Flyer-Design für Immobilienmakler & Bauträger
Zielgruppe
Wir sind Immobilienmakler & Bauträger
Zielgruppe sind alle, die eine Immobile besitzen und (jetzt oder später) verkaufen möchten
Wir möchten vermehrt Werbung in den lokalen Ortszeitungen machen um bekannter zu werden!
Bei der Vielzahl von Maklern möchten wir hervorstechen und uns auch von den ganzen Franchise Unternhemen abheben
Als kleines Familienunternhemen steht bei uns neben einer erfolgreichen Vermarktung Zuverlässigkeit, Fairness und Freundlichkeit an oberster Stelle!
WOCA (WOhnwerk CAstagno) besteht aus
Heribert Castagno (Geschäftsführer)
Petra Castagno (Tochter)
Jonas Castagno (Sohn)
Aufgabenstellung
Heidelberg und die Umgebung soll uns als freundliches, zuverlässiges & erfolgreiches Maklerteam kennenlernen, hierfür benötigen wir einen Flyer mit Vorder- und Rückseite
Die Vorderseite soll übersichtlich sein und auf den ersten Blick erkennen lassen
- wer wir sind (gerne auch mit Bildern von uns - diese sollen später von uns durch aktuelle ersetzt werden können)
- was wir suchen (zum Verkauf stehende Objekte - sowohl zur Vermarktung als auch zum Eigenankauf)
- was wir können - bzw was wir tun - Immobilien erfolgreich vermitteln/vermarkeln - für Auftraggeber kostenfrei!!
Gerne auch mit
'Ihr freundliches Immobilienbüro im Herzen von Neuenheim'
Wir haben ebenfalls eine Bauträgergesellschaft, vll könnte man auch dieses Logo mit einfließen lassen
KTR GmbH
Auf der Rückseite soll das Thema Tippgeber aufgegriffen werden -
Ihr Wissen ist bares Geld wert
oder
Wir belohnen Ihr Wissen
Ihre Freunde, Bekannte, Verwandte, Nachbarn oder Vermieter haben Ihnen von Verkaufsplänen ihrer Immobilie erzählt?
Geben Sie den Tipp an uns weiter! Führt dieser zum Verkauf der benannten Immobilie durch uns, ist uns das 10% unserer Maklerprovision (netto) wert.
Und so geht’s:
1. Sie melden sich per E-Mail, Telefon oder über das Homepage-Formular und benennen den Eigentümer und das Objekt, welches verkauft werden soll. Teilen Sie in diesem Rahmen auch mit, ob Ihr Tipp anonym behandelt werden soll.
2. Wir setzen uns mit dem Eigentümer in Verbindung
3. Sie erhalten von uns eine Information
4. Nach erfolgreichen Verkauf erhalten Sie Ihre Tippgeberprovision gutgeschrieben.
Die Tippgebervergütungen werden nach Abschluss der Verträge und nach Eingang der Maklerprovision innerhalb von 7 Tagen ausbezahlt. Bei unterlassener Zahlung der Maklerprovision an uns kann auch keine Auszahlung der Tippgeberprovision erfolgen. Bei mehreren Tipps zu ..

```html
<!DOCTYPE html>
<html lang="de">
<head>
<meta charset="utf-8">
<title>Wohnwerk Castagno – Flyer</title>
<link href="https://fonts.googleapis.com/css2?family=Nunito:wght@400;600;700;800&family=Dancing+Script:wght@500&display=swap" rel="stylesheet">
<style>
  :root {
    --green: #1f7d4e;
    --green-dark: #176a40;
    --ink: #2d2d2d;
    --grey-panel: #e4e4e4;
    --backdrop: #4a4a4a;
    --white: #ffffff;
    --muted: #555555;
  }
  * { box-sizing: border-box; margin: 0; padding: 0; }
  html, body { width: 1200px; height: 1200px; overflow: hidden; }
  body {
    background: var(--backdrop);
    font-family: "Nunito", Arial, sans-serif;
    color: var(--ink);
    position: relative;
  }
  .card {
    position: absolute;
    left: 77px;
    width: 1046px;
    background: var(--white);
    box-shadow: 0 6px 18px rgba(0,0,0,.45);
    overflow: hidden;
  }
  .card--front { top: 53px; height: 523px; }
  .card--back { top: 605px; height: 518px; }

  .script {
    font-family: "Dancing Script", cursive;
    color: var(--green);
    font-weight: 500;
  }
  .tagline {
    position: absolute; left: 40px; top: 24px;
    font-size: 26px; white-space: nowrap;
  }
  .tagline-rule {
    position: absolute; left: 0; top: 66px; width: 520px;
    height: 1px; background: var(--green);
  }
  .brand {
    position: absolute; right: 44px; top: 40px;
    display: flex; align-items: center; gap: 10px;
  }
  .brand-mark { width: 18px; height: 18px; border-radius: 50%; background: var(--green); }
  .brand-name { font-size: 25px; font-weight: 800; color: var(--ink); letter-spacing: .3px; white-space: nowrap; }

  .team-band {
    position: absolute; left: 0; top: 91px; width: 560px; height: 211px;
    background: var(--green);
  }
  .member {
    position: absolute; top: 20px; width: 130px; text-align: center; color: var(--white);
  }
  .member-photo {
    width: 104px; height: 112px; margin: 0 auto 8px;
    background: linear-gradient(160deg, #cfcfcf, #8e8e8e);
  }
  .member-name { font-size: 15px; font-weight: 700; }
  .member-role { font-size: 11px; }

  .intro-marker { position: absolute; left: 0; top: 324px; width: 30px; height: 36px; background: var(--green); }
  .heading {
    font-weight: 700; font-size: 27px; color: var(--ink); letter-spacing: .5px;
  }
  .intro { position: absolute; left: 50px; top: 322px; width: 470px; }
  .intro p { font-size: 16px; line-height: 1.45; margin-top: 12px; color: var(--muted); }

  .panel {
    position: absolute; background: var(--grey-panel);
  }
  .panel::after {
    content: ""; position: absolute; right: 0; top: 0; width: 18px; height: 100%;
    background: var(--green);
  }
  .panel--offer { left: 552px; top: 151px; width: 494px; height: 336px; padding: 30px 40px 0 44px; }
  .panel--offer p { font-size: 17px; line-height: 1.45; color: var(--muted); margin: 10px 0 22px; }
  .panel--offer .highlight { color: var(--green); font-weight: 700; font-size: 15px; margin-top: 6px; }
  .panel--offer p.tight { margin-bottom: 2px; }

  /* back */
  .reward-band {
    position: absolute; left: 0; top: 15px; width: 451px; height: 208px;
    background: var(--green); color: var(--white); padding: 30px 34px 0 40px;
  }
  .reward-band .heading { color: var(--white); font-size: 25px; }
  .reward-band p { font-size: 13px; line-height: 1.45; margin-top: 12px; }
  .contact { position: absolute; left: 40px; top: 250px; }
  .contact li { list-style: none; display: flex; align-items: center; gap: 14px; font-size: 15px; color: var(--muted); height: 26px; }
  .contact li strong { color: var(--ink); }
  .contact svg { width: 18px; height: 18px; fill: var(--green); flex: none; }
  .contact .address { align-items: flex-start; height: auto; margin-bottom: 8px; line-height: 1.35; }
  .contact .gap { height: 12px; }

  .greeting { position: absolute; right: 50px; top: 14px; font-size: 28px; }
  .panel--steps { left: 480px; top: 74px; width: 566px; height: 330px; padding: 28px 40px 0 40px; }
  .step { display: flex; gap: 20px; margin-top: 14px; align-items: flex-start; }
  .step svg { width: 40px; height: 32px; flex: none; fill: var(--green); }
  .step p { font-size: 13px; line-height: 1.4; color: var(--muted); }
  .step b { color: var(--green); }
  .footnote {
    position: absolute; left: 508px; top: 420px; width: 490px;
    font-size: 10px; line-height: 1.4; color: var(--muted);
  }
</style>
</head>
<body>

<section class="card card--front">
  <div class="tagline script">Ihr freundliches Immobilienbüro im Herzen von Neuenheim</div>
  <div class="tagline-rule"></div>

  <div class="brand">
    <span class="brand-mark"></span>
    <span class="brand-name">Wohnwerk Castagno</span>
  </div>

  <div class="team-band">
    <div class="member" style="left:70px">
      <div class="member-photo" role="img" aria-label="Porträtfoto von Heribert Castagno"></div>
      <div class="member-name">Heribert Castagno</div>
      <div class="member-role">Geschäftsführer</div>
    </div>
    <div class="member" style="left:209px">
      <div class="member-photo" role="img" aria-label="Porträtfoto von Petra Castagno"></div>
      <div class="member-name">Petra Castagno</div>
      <div class="member-role">Immobilienberaterin</div>
    </div>
    <div class="member" style="left:353px">
      <div class="member-photo" role="img" aria-label="Porträtfoto von Jonas Castagno"></div>
      <div class="member-name">Jonas Castagno</div>
      <div class="member-role">Immobilienberater</div>
    </div>
  </div>

  <div class="intro-marker"></div>
  <div class="intro">
    <h2 class="heading">WER WIR SIND</h2>
    <p>Als kleines Familienunternehmen steht bei uns neben einer erfolgreichen Vermarktung Zuverlässigkeit, Fairness und Freundlichkeit an oberster Stelle!</p>
  </div>

  <div class="panel panel--offer">
    <h2 class="heading">WAS WIR SUCHEN</h2>
    <p>zum Verkauf stehende Objekte - sowohl zur Vermarktung als auch zum Eigenankauf</p>
    <h2 class="heading">WAS WIR TUN</h2>
    <p class="tight">Immobilien erfolgreich vermitteln und vermarkeln</p>
    <p class="highlight">FÜR AUFTRAGGEBER KOSTENFREI!!</p>
  </div>
</section>

<section class="card card--back">
  <div class="reward-band">
    <h2 class="heading">WIR BELOHNEN IHR WISSEN</h2>
    <p>Ihre Freunde, Bekannte, Verwandte, Nachbarn oder Vermieter haben Ihnen von Verkaufsplänen ihrer Immobilie erzählt?</p>
    <p>Geben Sie den Tipp an uns weiter! Führt dieser zum Verkauf der benannten Immobilie durch uns, ist uns das 10% unserer Maklerprovision (netto) wert.</p>
  </div>

  <ul class="contact">
    <li class="address">
      <svg viewBox="0 0 24 24"><path d="M12 2a7 7 0 0 0-7 7c0 5 7 13 7 13s7-8 7-13a7 7 0 0 0-7-7zm0 9.5A2.5 2.5 0 1 1 12 6.5a2.5 2.5 0 0 1 0 5z"/></svg>
      <span><strong>Wohnwerk Castagno</strong><br>Uferweg 14<br>69120 Heidelberg – Neuenheim</span>
    </li>
    <li><svg viewBox="0 0 24 24"><path d="M6.6 10.8a15 15 0 0 0 6.6 6.6l2.2-2.2a1 1 0 0 1 1-.25 11.4 11.4 0 0 0 3.6.57 1 1 0 0 1 1 1V20a1 1 0 0 1-1 1A17 17 0 0 1 3 4a1 1 0 0 1 1-1h3.5a1 1 0 0 1 1 1c0 1.25.2 2.45.57 3.6a1 1 0 0 1-.25 1z"/></svg>+49 (0) 6221 / 40 27 519</li>
    <li><svg viewBox="0 0 24 24"><path d="M6 3h12v5H6zM4 9h16a2 2 0 0 1 2 2v6h-4v4H6v-4H2v-6a2 2 0 0 1 2-2zm4 7v3h8v-3z"/></svg>+49 (0) 6221 / 40 27 520</li>
    <li class="gap"></li>
    <li><svg viewBox="0 0 24 24"><path d="M2 5h20v14H2zm2 2v.5l8 5 8-5V7l-8 5z"/></svg>scout@wohnwerk-castagno.de</li>
    <li><svg viewBox="0 0 24 24"><path d="M12 2a10 10 0 1 0 0 20 10 10 0 0 0 0-20zm6.9 6h-3a15 15 0 0 0-1.3-4A8 8 0 0 1 18.9 8zM12 4c.8 1.2 1.5 2.5 1.9 4h-3.8c.4-1.5 1.100-2.8 1.9-4zM4.3 14a8 8 0 0 1 0-4h3.4a16 16 0 0 0 0 4zm.8 2h3a15 15 0 0 0 1.3 4A8 8 0 0 1 5.1 16zm3-8h-3a8 8 0 0 1 4.3-4A15 15 0 0 0 8.1 8zM12 20c-.8-1.2-1.5-2.5-1.9-4h3.8c-.4 1.5-1.1 2.8-1.9 4zm2.3-6H9.7a14 14 0 0 1 0-4h4.6a14 14 0 0 1 0 4zm.3 6a15 15 0 0 0 1.3-4h3a8 8 0 0 1-4.3 4zm1.7-6a16 16 0 0 0 0-4h3.4a8 8 0 0 1 0 4z"/></svg>www.wohnwerk-castagno.de</li>
  </ul>

  <div class="greeting script">Wir freuen uns auf Ihre Kontaktaufnahme!</div>

  <div class="panel panel--steps">
    <h2 class="heading">UND SO GEHT'S</h2>
    <div class="step">
      <svg viewBox="0 0 40 32"><rect x="2" y="2" width="22" height="15" rx="6"/><path d="M8 17l-3 6 8-6z"/><rect x="16" y="12" width="22" height="15" rx="6" fill="#fff" stroke="#1f7d4e" stroke-width="2"/></svg>
      <p><b>1.</b> Sie melden sich per E-Mail, Telefon oder über das Homepage-Formular und benennen den Eigentümer und das Objekt, welches verkauft werden soll. Teilen Sie in diesem Rahmen auch mit, ob Ihr Tipp anonym behandelt werden soll.</p>
    </div>
    <div class="step">
      <svg viewBox="0 0 40 32"><rect x="2" y="4" width="24" height="16" rx="7"/><path d="M8 20l-3 7 9-7z"/><rect x="22" y="10" width="16" height="12" rx="5"/></svg>
      <p><b>2.</b> Wir setzen uns mit dem Eigentümer in Verbindung</p>
    </div>
    <div class="step">
      <svg viewBox="0 0 40 32"><circle cx="20" cy="14" r="11"/><path d="M14 22l-4 8 9-6z"/><rect x="19" y="8" width="2.5" height="9" fill="#fff"/><circle cx="20.2" cy="20" r="1.5" fill="#fff"/></svg>
      <p><b>3.</b> Sie erhalten von uns eine Information</p>
    </div>
    <div class="step">
      <svg viewBox="0 0 40 32"><circle cx="20" cy="16" r="13"/><text x="20" y="22" text-anchor="middle" font-family="Nunito, sans-serif" font-size="16" font-weight="800" fill="#fff">€</text></svg>
      <p><b>4.</b> Nach erfolgreichem Verkauf erhalten Sie Ihre Tippgeberprovision* gutgeschrieben.</p>
    </div>
  </div>

  <p class="footnote">*Die Tippgebervergütungen werden nach Abschluss der Verträge und nach Eingang der Maklerprovision innerhalb von 7 Tagen ausbezahlt. Bei unterlassener Zahlung der Maklerprovision an uns kann auch keine Auszahlung der Tippgeberprovision erfolgen. Bei mehreren Tipps zu einem Objekt, erhält nur der erste Tippgeber die Provision.</p>
</section>

</body>
</html>
```